Stonebridge Building and Projects business cards

A business card with watermark background (construction work)

Company logo attached

Home improvement projects
House renovations
Bathroom and kitchen renovations
House extensions
New builds and granny flats

Director Omar Haddani
(Phone number)
omar@sbpbuilding.com.au
(Instagram logo) sbp_building

```html
<!DOCTYPE html>
<html lang="en">
<head>
<meta charset="utf-8">
<title>Stonebridge Building and Projects – Business Cards</title>
<link href="https://fonts.googleapis.com/css2?family=Roboto:wght@400;500;700&family=Fira+Sans+Condensed:wght@600&family=Arvo&display=swap" rel="stylesheet">
<style>
  :root {
    --page-bg: #2b2b2b;
    --card-dark: #0d0f12;
    --card-light: #fafafa;
    --brand-blue: #0a79c2;
    --ink: #333a40;
    --white: #ffffff;
    --rule: #1a82c9;
  }
  * { margin: 0; padding: 0; box-sizing: border-box; }
  html, body { width: 1138px; height: 1200px; overflow: hidden; }
  body {
    background: var(--page-bg);
    font-family: "Roboto", Arial, sans-serif;
    position: relative;
  }
  .card {
    position: absolute;
    top: 289px;
    width: 376px;
    height: 622px;
    border-radius: 16px;
    overflow: hidden;
    text-align: center;
  }
  .card--front { left: 162px; background: var(--card-dark); color: var(--white); }
  .card--back { left: 600px; background: var(--card-light); color: var(--ink); }

  .watermark {
    position: absolute; inset: 0 0 46px 0;
    background: radial-gradient(ellipse at 55% 40%, #1d2127 0%, #121418 55%, #0b0c0f 100%);
  }

  .brand { position: absolute; left: 0; right: 0; }
  .brand__name {
    font-family: "Roboto", Arial, sans-serif;
    font-weight: 700;
    color: var(--brand-blue);
    font-size: 38px;
    line-height: 1;
    letter-spacing: 0.5px;
  }
  .brand__sub {
    display: flex; align-items: center; justify-content: center; gap: 8px;
    font-family: "Roboto", Arial, sans-serif;
    font-weight: 700;
    font-size: 12.5px;
    letter-spacing: 4.5px;
    text-transform: uppercase;
    margin-top: 10px;
  }
  .brand__sub::before, .brand__sub::after {
    content: ""; width: 34px; height: 2px; background: var(--rule);
  }
  .brand__tagline {
    display: inline-block;
    font-family: "Arvo", Georgia, serif;
    color: var(--brand-blue);
    font-size: 18px;
    margin-top: 10px;
    padding-bottom: 3px;
    border-bottom: 2px solid var(--rule);
  }
  .card--front .brand { top: 150px; }
  .card--front .brand__sub { color: var(--white); }
  .card--back .brand { top: 128px; }
  .card--back .brand__sub { color: var(--ink); }

  .services { position: absolute; top: 362px; left: 0; right: 0; list-style: none; font-size: 16px; }
  .services li { height: 32px; line-height: 30px; }
  .services li span { display: inline-block; padding: 0 8px; border-bottom: 1.5px solid var(--rule); }
  .services li.pair span { border-bottom: none; }
  .services .divider { color: var(--brand-blue); margin: 0 4px; }

  .social {
    position: absolute; left: 0; right: 0;
    display: flex; align-items: center; justify-content: center; gap: 10px;
    font-size: 16px;
  }
  .social__dot { width: 15px; height: 15px; border-radius: 50%; background: #c13584; }
  .card--front .social { top: 517px; }
  .card--back .social { top: 538px; color: var(--ink); }

  .footer-band {
    position: absolute; left: 0; right: 0; bottom: 0; height: 46px;
    background: var(--brand-blue);
    font-size: 16px; line-height: 46px; color: var(--white);
  }

  .person { position: absolute; top: 330px; left: 0; right: 0; }
  .person__name {
    font-family: "Fira Sans Condensed", Arial, sans-serif;
    font-weight: 600; font-size: 26px; color: var(--brand-blue);
  }
  .person__role { font-size: 16px; margin-top: 4px; }

  .icon-row {
    position: absolute; top: 408px; left: 0; right: 0;
    display: flex; align-items: center; justify-content: center; gap: 4px;
  }
  .icon-row__rule { width: 48px; height: 2px; background: var(--ink); margin: 0 14px; }
  .contact-icon { width: 24px; height: 24px; }

  .contacts { position: absolute; top: 448px; left: 0; right: 0; font-size: 16px; line-height: 24.5px; }
  .contacts .highlight { color: var(--brand-blue); }
</style>
</head>
<body>

<section class="card card--front">
  <div class="watermark" role="img" aria-label="Faint background photo of a building under construction"></div>
  <div class="brand">
    <div class="brand__name">Stonebridge</div>
    <div class="brand__sub">Building and Projects</div>
    <div class="brand__tagline">Built from the ground up!</div>
  </div>
  <ul class="services">
    <li><span>Home Improvement Projects</span></li>
    <li><span>Bathroom &amp; Kitchen Renovations</span></li>
    <li><span>New Builds &amp; Granny Flats</span></li>
    <li class="pair"><span>House Renovations <b class="divider">|</b> House Extensions</span></li>
  </ul>
  <div class="social"><i class="social__dot"></i>sbp_building</div>
  <div class="footer-band">www.sbpbuilding.com.au</div>
</section>

<section class="card card--back">
  <div class="brand">
    <div class="brand__name">Stonebridge</div>
    <div class="brand__sub">Building and Projects</div>
    <div class="brand__tagline">Built from the ground up!</div>
  </div>
  <div class="person">
    <div class="person__name">Omar Haddani</div>
    <div class="person__role">Managing Director</div>
  </div>
  <div class="icon-row">
    <span class="icon-row__rule"></span>
    <svg class="contact-icon" viewBox="0 0 24 24" aria-label="Phone"><circle cx="12" cy="12" r="11" fill="none" stroke="#0a79c2" stroke-width="1.6"/><path d="M7 9c0-1.5 2.5-2.5 5-2.5S17 7.5 17 9l-1.8.8-1-1.4h-4.4l-1 1.4zM8.5 11h7l1 5h-9z" fill="#0a79c2"/><circle cx="12" cy="13.5" r="1.4" fill="#fafafa"/></svg>
    <svg class="contact-icon" viewBox="0 0 24 24" aria-label="Email"><circle cx="12" cy="12" r="11" fill="none" stroke="#0a79c2" stroke-width="1.6"/><rect x="6.5" y="8" width="11" height="8" rx="1" fill="#0a79c2"/><path d="M6.8 8.4 12 12.5l5.2-4.1" fill="none" stroke="#fafafa" stroke-width="1.2"/></svg>
    <svg class="contact-icon" viewBox="0 0 24 24" aria-label="Website"><circle cx="12" cy="12" r="11" fill="none" stroke="#0a79c2" stroke-width="1.6"/><g fill="none" stroke="#0a79c2" stroke-width="1.2"><circle cx="12" cy="12" r="5.5"/><ellipse cx="12" cy="12" rx="2.3" ry="5.5"/><path d="M6.5 12h11M7.3 9.3h9.4M7.3 14.7h9.4"/></g></svg>
    <span class="icon-row__rule"></span>
  </div>
  <div class="contacts">
    <div>0412 555 018</div>
    <div>omar@sbpbuilding.com.au</div>
    <div>www.<span class="highlight">sbpbuilding</span>.com.au</div>
  </div>
  <div class="social"><i class="social__dot"></i>sbp_building</div>
</section>

</body>
</html>
```